New digital business consulting firm needs a professional Wordpress site

Bluefern Advisory Inc. is a new consulting firm that helps large companies with Digital Transformation. We help companies define a digital transformation strategy for improving the products, processes and customer journey using digital technology.

The website will serve three purposes:
1) Represent what the firm does.
2) Allow people to download research reports.
3) Collect email addresses from people who my be interested in using our services.

The tone of the website should be innovative and professional. The website will have only a few pages. You can see the type of content we wish to post on the current website www.bluefernadvisory.com.

The website will support a book that is about to be released. The book cover is attached. However, the website does not necessarily have to match the book cover. Do not be constrained by the book cover.

Target Market(s)

Executives in large companies

Industry/Entity Type

Management Consulting

Font styles to use
Sans Serif

Requirements
Must have
• Professional and innovative, clean, cool
Nice to have
• None
Should not have
• None

```html
<!DOCTYPE html>
<html lang="en">
<head>
<meta charset="utf-8">
<title>Bluefern Advisory</title>
<link href="https://fonts.googleapis.com/css2?family=Open+Sans:wght@400;600;700&family=Lobster&display=swap" rel="stylesheet">
<style>
:root{
  --blue:#1c4f87;
  --navy:#123f73;
  --blue-deep:#0f355f;
  --green:#6b9a3c;
  --ink:#222;
  --muted:#777;
  --card:#f3f3f3;
  --field:#f1f1f1;
  --line:#dcdcdc;
  --paper:#f2f2f2;
  --white:#fff;
}
*{box-sizing:border-box;margin:0;padding:0}
html,body{width:1200px;height:2857px;overflow:hidden}
body{position:relative;background:var(--white);font-family:"Open Sans",Arial,sans-serif;color:var(--ink)}
.abs{position:absolute}
.script{font-family:"Lobster",cursive}

/* header */
.topline{top:0;left:0;width:1200px;height:3px;background:var(--green)}
.brand{top:44px;left:90px;font-size:38px;font-weight:600;color:var(--blue);letter-spacing:-.5px}
.nav{top:76px;left:532px;display:flex;gap:48px;font-size:15px;color:#333}
.nav .active{color:var(--blue);font-weight:700}
.search{top:64px;left:1072px;width:42px;height:42px;border:2px solid var(--green);border-radius:50%}

/* hero */
.hero{top:120px;left:0;width:1200px;height:505px}
.hero-photo{position:absolute;inset:0;background:linear-gradient(100deg,#1e2f48 0%,#44628a 35%,#7d98b8 60%,#3b5576 100%)}
.hero-title{top:308px;left:86px;font-size:36px;font-weight:700;color:var(--white);text-shadow:0 2px 4px rgba(0,0,0,.3)}
.hero-btn{top:384px;left:86px;width:118px;height:42px;background:var(--green);color:var(--white);font-size:14px;font-weight:700;border-radius:4px;display:flex;align-items:center;justify-content:center}
.hero-arrow{top:356px}
.hero-base{top:622px;left:0;width:1200px;height:3px;background:var(--green)}

/* services */
.sec-title{left:0;width:1200px;text-align:center;font-weight:600;color:var(--ink)}
.sec-sub{left:0;width:1200px;text-align:center;color:var(--muted)}
.card{top:825px;width:244px;height:291px;background:var(--card);border-radius:6px;box-shadow:0 3px 6px rgba(0,0,0,.12);text-align:center}
.card .icon{position:absolute;top:47px;left:74px;width:96px;height:96px;border-radius:50%;background:var(--blue);border:3px solid var(--white);box-shadow:0 0 0 2px var(--blue)}
.card h3{position:absolute;top:160px;left:0;width:100%;font-size:15px;font-weight:600}
.card p{position:absolute;top:188px;left:20px;width:204px;font-size:12px;line-height:19px;color:var(--muted)}
.card .more{position:absolute;top:233px;left:0;width:100%;font-size:11px;font-weight:700;color:var(--blue)}

/* book */
.book-band{top:1212px;left:0}
.book-title{top:1336px;left:90px;font-size:32px;font-weight:700;color:var(--white)}
.book-copy{top:1398px;left:90px;width:672px;font-size:13px;line-height:24px;color:var(--white)}
.book-note{top:1548px;left:90px;font-size:26px;color:var(--white)}
.btn-outline{background:var(--white);color:var(--navy);border-radius:8px;box-shadow:0 0 0 3px var(--navy),0 0 0 5px var(--white);display:flex;align-items:center;justify-content:center;font-size:16px}
.btn-dark{background:var(--navy);color:var(--white);border-radius:8px;box-shadow:0 0 0 2px var(--white),0 0 0 4px var(--navy);display:flex;align-items:center;justify-content:center;font-size:16px}
.cover-frame{top:1330px;left:842px;width:266px;height:310px;border:3px solid var(--white);background:#e9e9ea;padding:32px 44px}
.cover{width:100%;height:100%;background:linear-gradient(180deg,#0e1e3e,#1a2b52)}

/* research */
.research{top:1728px;left:0;width:1200px;height:287px;background:var(--paper)}

/* form */
.field{width:322px;height:44px;background:var(--field);border:1px solid var(--line);border-radius:8px;padding-left:38px;font-size:13px;color:#555;display:flex;align-items:center}

/* footer */
.footer-band{top:2457px;left:0}
.f-col{top:2572px}
.f-col h4{font-size:17px;font-weight:600;color:var(--white);margin-bottom:22px}
.f-col li{list-style:none;font-size:13px;color:var(--white);height:34px;display:flex;align-items:flex-start;gap:14px}
.f-col.social li{height:42px;align-items:center}
.dot{width:30px;height:30px;border:1.5px solid var(--white);border-radius:50%;flex:none}
.copyright{top:2816px;left:0;width:1200px;height:41px;background:#ececec;font-size:12px;color:#444;display:flex;align-items:center;justify-content:center}
</style>
</head>
<body>

<div class="abs topline"></div>
<div class="abs brand">Bluefern Advisory</div>
<nav class="abs nav"><span class="active">HOME</span><span>BOOK</span><span>SERVICES</span><span>DOWNLOADABLE RESEARCH</span></nav>
<div class="abs search">
  <svg width="38" height="38" viewBox="0 0 38 38"><circle cx="17.5" cy="17.5" r="5" fill="none" stroke="#6b9a3c" stroke-width="2"/><line x1="21" y1="21" x2="25" y2="25" stroke="#6b9a3c" stroke-width="2.4"/></svg>
</div>

<section class="abs hero">
  <div class="hero-photo" role="img" aria-label="Photo of a hand touching a digital interface with charts and icons"></div>
  <svg class="abs" style="top:0;left:0" width="1200" height="505"><polygon points="0,0 1200,0 1200,70" fill="#fff"/></svg>
</section>
<h1 class="abs hero-title">WELCOME TO BLUEFERN ADVISORY</h1>
<div class="abs hero-btn">READ MORE</div>
<svg class="abs hero-arrow" style="left:38px" width="20" height="34"><polyline points="16,2 4,17 16,32" fill="none" stroke="rgba(255,255,255,.6)" stroke-width="2"/></svg>
<svg class="abs hero-arrow" style="left:1142px" width="20" height="34"><polyline points="4,2 16,17 4,32" fill="none" stroke="rgba(255,255,255,.6)" stroke-width="2"/></svg>
<div class="abs hero-base"></div>

<h2 class="abs sec-title" style="top:700px;font-size:23px">OUR SERVICES</h2>
<p class="abs sec-sub" style="top:748px;font-size:13px">Our associate consultants, can be retained for the following services</p>

<div class="abs card" style="left:187px">
  <div class="icon"><svg width="90" height="90" viewBox="0 0 90 90"><circle cx="45" cy="34" r="8" fill="#fff"/><rect x="33" y="44" width="24" height="10" rx="4" fill="#fff"/><rect x="28" y="56" width="34" height="6" fill="#fff"/></svg></div>
  <h3>Speaking Engagements</h3>
  <p>Provide an overview of the digital technology and implications</p>
  <div class="more">READ MORE ➜</div>
</div>
<div class="abs card" style="left:478px">
  <div class="icon"><svg width="90" height="90" viewBox="0 0 90 90"><path d="M38 30v20l-5-4-3 3 10 12h16l3-14-13-4V30z" fill="#fff"/></svg></div>
  <h3>Digital Assessment</h3>
  <p>Help your company the state of your digital transformation</p>
  <div class="more">READ MORE ➜</div>
</div>
<div class="abs card" style="left:769px">
  <div class="icon"><svg width="90" height="90" viewBox="0 0 90 90"><rect x="29" y="30" width="32" height="26" fill="none" stroke="#fff" stroke-width="3"/><polyline points="32,52 40,42 46,48 52,40 58,52" fill="#fff"/><rect x="25" y="58" width="40" height="4" fill="#fff"/></svg></div>
  <h3>Digital Strategy Development</h3>
  <p>Based on the digital assessment and your objective tation.</p>
  <div class="more">READ MORE ➜</div>
</div>

<svg class="abs book-band" width="1200" height="516" role="img" aria-label="Blue tinted photo of a person working with business charts">
  <defs><linearGradient id="bookBg" x1="0" y1="0" x2="1" y2="1"><stop offset="0" stop-color="#1a4a7f"/><stop offset="1" stop-color="#0f3d72"/></linearGradient></defs>
  <polygon points="0,74 1200,0 1200,516 0,516" fill="url(#bookBg)"/>
</svg>
<h2 class="abs book-title">Book</h2>
<p class="abs book-copy">Leading Digital Well is a manual for winning in the next digital era. Its author, Martin Delacroix, has been helping large companies establish and execute digital strategies for 25 years.It is critical for any executive in any function to understand key digital technologies, the way they are evolving, how companies can leverage them to improve products, processes, and the customer journey, and what kind of business outcomes can be derived. All of that, moreover, is useless without knowing how to help your company define its digital vision and how to act on it. This book covers those topics to help you thrive in the new digital era.</p>
<p class="abs book-note script">The book will be available on Pagewise in January, 2017.</p>
<div class="abs btn-outline script" style="top:1610px;left:92px;width:118px;height:46px">Read More</div>
<div class="abs cover-frame"><div class="cover" role="img" aria-label="Book cover of Leading Digital Well"></div></div>

<section class="abs research">
  <h2 class="abs sec-title" style="top:62px;font-size:32px;font-weight:400">DOWNLOADABLE RESEARCH</h2>
  <p class="abs sec-sub" style="top:110px;font-size:20px;color:#444">We will be adding resources over time.</p>
  <div class="abs btn-dark script" style="top:168px;left:534px;width:132px;height:44px">Download Now</div>
</section>

<h2 class="abs sec-title" style="top:2090px;font-size:23px">CONTACT FORM</h2>
<p class="abs sec-sub" style="top:2138px;font-size:13px">Please Fill all the details in the form below.</p>
<div class="abs field" style="top:2208px;left:269px">First Name</div>
<div class="abs field" style="top:2208px;left:610px">Last Name</div>
<div class="abs field" style="top:2277px;left:269px">Email</div>
<div class="abs field" style="top:2277px;left:610px">Organization</div>
<div class="abs btn-dark" style="top:2360px;left:544px;width:114px;height:44px;font-size:15px;font-weight:700">SUBMIT</div>

<svg class="abs footer-band" width="1200" height="360" role="img" aria-label="Blue tinted photo of a business meeting">
  <polygon points="0,0 1200,77 1200,360 0,360" fill="#1c4d85"/>
  <line x1="0" y1="0" x2="1200" y2="77" stroke="#6b9a3c" stroke-width="3"/>
</svg>

<div class="abs f-col" style="left:110px">
  <h4>CONTACT US</h4>
  <ul>
    <li style="height:50px"><svg width="16" height="14"><polygon points="8,1 15,7 13,7 13,13 3,13 3,7 1,7" fill="#fff"/></svg><span>1.10.32 .de Finibus Bonorum<br>et Malorum</span></li>
    <li><svg width="16" height="16"><rect x="4" y="1" width="8" height="14" rx="1.5" fill="#fff"/></svg><span>Call Us : (555)-014-2290</span></li>
    <li><svg width="16" height="14"><rect x="1" y="2" width="14" height="10" fill="none" stroke="#fff" stroke-width="1.5"/><polyline points="1,2 8,8 15,2" fill="none" stroke="#fff" stroke-width="1.5"/></svg><span>Mail Us : hello@bluefernadvisory.com</span></li>
  </ul>
</div>
<div class="abs f-col" style="left:423px">
  <h4>QUICK LINKS</h4>
  <ul><li>» <span>Home</span></li><li>» <span>Book</span></li><li>» <span>Services</span></li><li>» <span>Downloadable Research</span></li><li>» <span>Contact us</span></li></ul>
</div>
<div class="abs f-col" style="left:703px">
  <h4>OTHER LINKS</h4>
  <ul><li>» <span>Disclaimer</span></li><li>» <span>Terms &amp; Conditions</span></li><li>» <span>Privacy Policy</span></li><li>» <span>Policy</span></li><li>» <span>Sitemap</span></li></ul>
</div>
<div class="abs f-col social" style="left:964px">
  <h4>STAY IN TOUCH</h4>
  <ul><li><span class="dot"></span>Friendwall</li><li><span class="dot"></span>Chirpline</li><li><span class="dot"></span>Circleplus</li><li><span class="dot"></span>Snapgrid</li></ul>
</div>

<div class="abs copyright">@copyright 2017 Bluefern Advisory.All Rights Reserved</div>
</body>
</html>
```